Wholesale Catalogue Design for Greeting Cards

Fern Ink is a small letterpress printery, I would like to have a wholesale catalogue designed for my range of letterpress greeting cards. I currently have 30 cards in my collection, I can supply photos, I want to be able to add to the catalogue in the future. I also want the design to represent my card designs: fun, colourful and with an elegant edge, featuring a mix of my original illustrations and hand lettering along with downloadable designs and fonts.
I would like to be able to email the catalogue to my wholesale customers and to be able to print the catalogue to use with new/potential wholesale customers.

Target Market(s)

Small boutique retailers, gift shops, baby/kids gift shops, florists

Industry/Entity Type

Wholesale

Font styles to use
Serif

Colors
eea4c8

Requirements
Must have
• I have been using baskerville font in my branding, so it would be good to include this in the design. I can provide photos and text. I also have a pink and black logo (seen attached), it would be great if the design can incorporate some of the same colour scheme.
Nice to have
• I have added some pics below of other catalogues I like the layout of.
• You can also view my work at craftly.com/fernink or ferninkdesign.com
• * I believe I have now loaded all the relevant photos and info
• ** I have uploaded some pics of my attempt at a wholesale catalogue and my current order sheet as this outlines the products I want in the catalogue and the different card sections. my catalogue attempt has more recent photos. I will upload photos of the remaining products by end of today (27.2.16)

```html
<!DOCTYPE html>
<html lang="en">
<head>
<meta charset="UTF-8">
<title>Fern Ink — Wholesale Catalogue Back Cover</title>
<link rel="stylesheet" href="https://fonts.googleapis.com/css2?family=Libre+Baskerville:wght@400;700&display=swap">
<style>
  :root {
    --paper: #ffffff;
    --blush: #e8aeb0;
    --ink: #000000;
    --label-bg: #fbfafa;
    --on-blush: #ffffff;
  }
  html, body {
    margin: 0;
    padding: 0;
    overflow: hidden;
    background: var(--paper);
  }
  .cover {
    position: relative;
    width: 1200px;
    height: 918px;
    background: var(--paper);
    overflow: hidden;
  }
  .cover__shapes {
    position: absolute;
    inset: 0;
    width: 1200px;
    height: 918px;
  }
  .cover__wedge { fill: var(--blush); }
  .cover__edge {
    fill: none;
    stroke: var(--ink);
    stroke-width: 12;
    stroke-linejoin: miter;
  }
  .brand {
    position: absolute;
    left: 506px;
    top: 80px;
    width: 648px;
    height: 184px;
    background: var(--label-bg);
    display: flex;
    align-items: center;
    justify-content: center;
  }
  .brand__name {
    margin: 0;
    font-family: "Libre Baskerville", Baskerville, serif;
    font-weight: 400;
    font-size: 92px;
    letter-spacing: 1px;
    color: var(--ink);
  }
  .contact {
    position: absolute;
    left: 140px;
    top: 708px;
    margin: 0;
    font-family: "Libre Baskerville", Baskerville, serif;
    font-weight: 700;
    font-size: 25px;
    line-height: 33px;
    text-transform: uppercase;
    color: var(--on-blush);
    font-style: normal;
  }
  .contact__line { display: block; }
</style>
</head>
<body>
  <main class="cover">
    <svg class="cover__shapes" viewBox="0 0 1200 918" aria-hidden="true">
      <polygon class="cover__wedge" points="0,0 140,0 920,766 768,918 0,918"/>
      <polyline class="cover__edge" points="146,-10 928,766 774,928"/>
    </svg>

    <div class="brand">
      <h1 class="brand__name">Fern Ink</h1>
    </div>

    <address class="contact">
      <span class="contact__line">Fern Ink Mailing Address</span>
      <span class="contact__line">fernink@postmail.com</span>
      <span class="contact__line">www.fernink.com/au</span>
    </address>
  </main>
</body>
</html>
```